PowerPoint Listing Presentation for Real Estate Agency

We need a PowerPoint presentation for a new real estate brokerage team.

[[[[[[submit 1-3 sample slides for review - i will provide feedback and you can make changes if you want to - we will not be deciding on a design prior to the deadline]]]]]

******ATTN: DESIGNERS, if your skills are webdesign then just look at this like a portable website or a brochure. it should be easy enough******

NOTE: we have all the data to put into the slides. You just need to come up with the design and layout. we have a sample design that we like and have provided.

This focus will be for the home listing side of the business (a presentation for home sellers to convince them to use our services). The data and slides will present our team and the benefits, in the best light, to use our services over that of other real estate agent applying for the job. This presentation will proved facts and benefits and describe our special and unique offerings that will show a home seller why we can sell their home for more money in less time and with the least amount of hassle. The main color scheme is Dark Blue and White (we want some additional colors included - based on your creativity. otherwise the presentation will too monotone). We would like to see the use of Statistical Graphs (3-D) - data provided. We have photos of our team and a new logo (the logo could have some minor adjustment to clean it up if necessary) - also uploaded. We have about 80-90% of the information that will be put into the slides and will need to work closely to get the design and data integrated into the presentation (should be easier then it sounds). We should be able to add slides and data 'at will' over time via our master slides built into the presentation. We have a pretty good sample presentation that we like and can be used as a guideline (this is from our affiliated business network and we have full rights to all the information), it is uploaded but doesn't contain all the slide because of size limitations.

NOTE: An additional buyers presentation will be needed after we get the sellers presentation completed, which means additional work.

This should be enough to get you started and we are available if you have any questions to help you with the project. there will be around 60-70 total slides. once concept is completed it will be easy to create the slides.

Target Market(s)

home sellers. people who are moving to a new and better home or relocation for job reasons. typically more established in life

Industry/Entity Type

Real Estate

Requirements
Must have
• all the slides must be congruent. in other words, the exact same layout feel should used across the board. we are working on building our trade dress/image. Also, it must have a soft and inviting overall feel, yet show strength of ability.
Nice to have
• nice to have use of real people images when necessary. 3D graphs would be nice. clean modern look and feel, yet sophisticated and professional.
Should not have
• should not have a lot of time consuming transitions. do not include 3D stick figures or distracting moving gifs

```html
<!DOCTYPE html>
<html lang="en">
<head>
<meta charset="utf-8">
<title>VIP Seller Benefits</title>
<link rel="stylesheet" href="https://fonts.googleapis.com/css2?family=Gelasio:wght@400;700&family=Open+Sans:wght@700&family=Tinos:wght@700&display=swap">
<style>
  :root {
    --navy-deep: #0a2566;
    --navy: #123a8c;
    --navy-mid: #1f4fa6;
    --sky: #5d8fd6;
    --sky-soft: #a9c6ec;
    --page-top: #ffffff;
    --page-bottom: #d6e5f7;
    --ink: #1a1a2e;
    --accent-blue: #1740a0;
    --tick-orange: #f3a21c;
    --white: #ffffff;
  }
  * { margin: 0; padding: 0; box-sizing: border-box; }
  html, body { width: 1200px; height: 900px; overflow: hidden; }
  body { font-family: "Gelasio", Georgia, serif; }
  .slide {
    position: relative;
    width: 1200px; height: 900px;
    background: linear-gradient(180deg, var(--page-top) 20%, var(--page-bottom) 100%);
    overflow: hidden;
  }
  .slide-art { position: absolute; inset: 0; width: 1200px; height: 900px; }
  .brand-mark {
    position: absolute; left: 24px; top: 22px;
    width: 122px; height: 122px;
    border: 3px solid var(--white);
  }
  .team-name {
    position: absolute; left: 170px; top: 64px;
    font-size: 37px; line-height: 50px; color: var(--white); font-weight: 400;
  }
  .slide-title {
    position: absolute; right: 24px; top: 174px;
    font-size: 42px; line-height: 56px; font-weight: 400; color: var(--ink);
  }
  .slide-title .highlight { color: var(--accent-blue); }
  .benefits { position: absolute; left: 40px; top: 351px; list-style: none; }
  .benefit { position: relative; padding-left: 82px; font-size: 33px; color: var(--ink); line-height: 58px; }
  .benefit + .benefit { margin-top: 50px; }
  .benefit + .benefit { padding-left: 86px; }
  .benefit svg { position: absolute; left: 0; top: 4px; width: 54px; height: 54px; }
  .benefit .note {
    font-family: "Open Sans", Verdana, sans-serif;
    color: var(--accent-blue); font-weight: 700; font-size: 26px;
  }
  .benefit .shout {
    font-family: "Tinos", "Times New Roman", serif;
    color: var(--accent-blue); font-weight: 700; font-size: 27px;
  }
  .copyright {
    position: absolute; left: 58px; top: 846px;
    font-size: 16px; color: var(--white);
  }
  .homes-artwork {
    position: absolute; left: 905px; top: 748px;
    width: 285px; height: 122px;
  }
</style>
</head>
<body>
<main class="slide">
  <svg class="slide-art" viewBox="0 0 1200 900" aria-hidden="true">
    <defs>
      <linearGradient id="headerFill" x1="0" y1="0" x2="1" y2="0">
        <stop offset="0" stop-color="#0a2566"/>
        <stop offset="0.6" stop-color="#123a8c"/>
        <stop offset="1" stop-color="#1f4fa6"/>
      </linearGradient>
      <linearGradient id="footerFill" x1="0" y1="0" x2="1" y2="0">
        <stop offset="0" stop-color="#0a2566"/>
        <stop offset="1" stop-color="#163f96"/>
      </linearGradient>
      <linearGradient id="cornerFill" x1="0" y1="0" x2="0" y2="1">
        <stop offset="0" stop-color="#c4d9f3"/>
        <stop offset="1" stop-color="#9dbde8"/>
      </linearGradient>
      <radialGradient id="badgeFill" cx="0.4" cy="0.35" r="0.7">
        <stop offset="0" stop-color="#4f86d6"/>
        <stop offset="1" stop-color="#123a8c"/>
      </radialGradient>
      <linearGradient id="ruleFade" x1="0" y1="0" x2="1" y2="0">
        <stop offset="0" stop-color="#123a8c" stop-opacity="0"/>
        <stop offset="0.3" stop-color="#123a8c" stop-opacity="0.8"/>
        <stop offset="1" stop-color="#123a8c"/>
      </linearGradient>
    </defs>

    <path d="M0 0 H1200 V150 C980 125 760 140 560 180 C380 215 180 232 0 226 Z" fill="#5d8fd6"/>
    <path d="M0 0 H1200 V138 C980 112 760 128 560 168 C380 203 180 220 0 214 Z" fill="#ffffff"/>
    <path d="M0 0 H1200 V128 C980 100 760 116 560 156 C380 192 180 208 0 202 Z" fill="url(#headerFill)"/>
    <path d="M0 0 H1200 V60 C1000 70 820 95 620 120 C420 145 200 120 0 110 Z" fill="#1f4fa6" opacity="0.35"/>

    <rect x="520" y="234" width="680" height="3" fill="url(#ruleFade)"/>
    <circle cx="642" cy="202" r="35" fill="#ffffff"/>
    <circle cx="642" cy="202" r="31" fill="url(#badgeFill)"/>
    <ellipse cx="642" cy="252" rx="26" ry="10" fill="#123a8c" opacity="0.12"/>

    <path d="M0 768 C300 758 560 790 760 900 H0 Z" fill="#ffffff"/>
    <path d="M0 782 C300 772 560 804 740 900 H0 Z" fill="#5d8fd6"/>
    <path d="M0 792 C300 782 560 814 720 900 H0 Z" fill="url(#footerFill)"/>
    <path d="M760 900 C900 860 1060 820 1200 790 V900 Z" fill="url(#cornerFill)"/>
    <path d="M700 900 C900 880 1060 872 1200 868 V900 Z" fill="#0a2566"/>
  </svg>

  <svg class="homes-artwork" viewBox="0 0 285 122" role="img" aria-label="Outline illustration of three house roofs in light and dark blue">
    <defs>
      <linearGradient id="homesTone" x1="0" y1="0" x2="1" y2="0">
        <stop offset="0" stop-color="#7fa8e2"/>
        <stop offset="0.5" stop-color="#6a6fc2"/>
        <stop offset="1" stop-color="#8fb6e8"/>
      </linearGradient>
    </defs>
    <rect width="285" height="122" fill="url(#homesTone)" opacity="0.55"/>
  </svg>

  <div class="brand-mark"></div>
  <div class="team-name">The Harrow &amp; Quinn Team</div>

  <h1 class="slide-title">Our VIP Seller <span class="highlight">Benefits</span></h1>

  <ul class="benefits">
    <li class="benefit">
      <svg viewBox="0 0 54 54" aria-hidden="true">
        <circle cx="24" cy="30" r="21" fill="var(--tick-orange)"/>
        <path d="M12 28 L22 40 L46 8" fill="none" stroke="#0a2566" stroke-width="8" stroke-linecap="round" stroke-linejoin="round"/>
      </svg>
      Your Home Sold at a Price Acceptable to You<br>
      <span class="note">(Guaranteed in Writing)</span> or We’ll Buy it for Cash!
    </li>
    <li class="benefit">
      <svg viewBox="0 0 54 54" aria-hidden="true">
        <circle cx="24" cy="30" r="21" fill="var(--tick-orange)"/>
        <path d="M12 28 L22 40 L46 8" fill="none" stroke="#0a2566" stroke-width="8" stroke-linecap="round" stroke-linejoin="round"/>
      </svg>
      Buy Any One of Our Listings and if YOU Are Not<br>
      Satisfied in 24 Months <span class="shout">WE’LL BUY IT BACK!</span>
    </li>
  </ul>

  <p class="copyright">Copyright Text here</p>
</main>
</body>
</html>
```